Website for Excavator and Earthworks Company

We require a modern, sleek and practical website for our newly created earthworks/excavator business in Perth, Western Australia called Bluegum Ridge Earthworks.

The website should have a modern, cutting edge feel but only needs to be relatively simplistic in it's layout and eventual functionality.

Some pages it should have would be Home, About, Projects and Contact Us.

```html
<!DOCTYPE html>
<html lang="en">
<head>
<meta charset="utf-8">
<title>Bluegum Ridge Earthworks</title>
<link href="https://fonts.googleapis.com/css2?family=Orbitron:wght@500;600;700&family=Lexend:wght@300;400;500&display=swap" rel="stylesheet">
<style>
:root{
  --lime:#c9dc12;
  --lime-pale:#f3f6d6;
  --cream:#fbfcef;
  --ink:#0a0a0a;
  --text:#2b2b2b;
  --white:#ffffff;
  --photo-warm:linear-gradient(135deg,#3a2a1c 0%,#a86a32 45%,#e6b774 60%,#4a3a2a 100%);
}
*{margin:0;padding:0;box-sizing:border-box}
html,body{width:1200px;height:3737px;overflow:hidden}
body{position:relative;background:var(--white);font-family:"Lexend",sans-serif;color:var(--text);font-weight:300}
.abs{position:absolute}
.display{font-family:"Orbitron",sans-serif;font-weight:600;text-transform:uppercase;letter-spacing:.5px}
.lime{color:var(--lime)}
.btn{position:absolute;display:flex;align-items:center;justify-content:center;gap:10px;border-radius:30px;background:var(--lime);color:var(--ink);font-size:13px;font-weight:400;text-transform:uppercase;text-decoration:none}
.btn svg{width:12px;height:12px}
.photo{position:absolute;overflow:hidden}

/* header */
.brand-box{left:135px;top:0;width:165px;height:99px;background:var(--white);border-radius:0 0 10px 10px;display:flex;align-items:center;justify-content:center;text-align:center;z-index:3;font-family:"Orbitron",sans-serif;font-weight:600;font-size:13px;line-height:1.3;color:var(--ink);text-transform:uppercase}
.nav{left:502px;top:32px;display:flex;gap:28px;font-size:14px;text-transform:uppercase;font-weight:400;color:var(--ink)}
.nav .active{color:var(--lime)}

/* hero */
.hero-photo{left:86px;top:77px;width:1028px;height:474px;border-radius:12px;background:var(--photo-warm);clip-path:path("M0 0 H1028 V474 H514 Q514 435 480 435 H0 Z")}
.hero-title{right:141px;top:122px;text-align:right;font-size:38px;color:var(--white);line-height:1.3}
.hero-title .lime{font-size:28px}
.hero-sub{right:141px;top:228px;width:300px;text-align:right;color:var(--white);font-size:16px;line-height:32px;font-weight:300}

/* about */
.about-mark{left:113px;top:640px;width:60px;height:60px;background:var(--lime)}
.about-title{left:258px;top:628px;font-size:27px;line-height:47px;color:var(--ink)}
.about-text{left:113px;width:436px;font-size:15.5px;line-height:32.6px;text-align:justify}
.dots{position:absolute;background-image:radial-gradient(circle,#6b6b6b 1.3px,transparent 1.6px);background-size:11.6px 11.6px}
.img-big{left:702px;top:637px;width:386px;height:424px;border-radius:28px;background:linear-gradient(160deg,#2e3a2a,#6f8a5a 40%,#d8793a 70%,#2a2e34)}
.img-small{left:605px;top:796px;width:251px;height:288px;border-radius:28px;border:5px solid var(--white);background:linear-gradient(170deg,#8fb4cf 0%,#c9c2a8 45%,#9a7450 70%,#e0672a 100%)}

/* services */
.services{left:78px;top:1167px;width:1044px;height:426px;background:var(--ink);border-radius:16px}
.service{position:absolute;top:1217px;color:var(--white)}
.service svg{width:50px;height:48px;display:block;margin-bottom:30px}
.service h3{font-family:"Lexend",sans-serif;font-weight:400;color:var(--lime);font-size:16px;line-height:32px;text-transform:uppercase;margin-bottom:10px}
.service p{font-size:15.5px;line-height:34px;font-weight:300}

/* why */
.why-card{left:132px;top:1502px;width:934px;height:573px;background:var(--white);border-radius:22px;box-shadow:0 6px 24px rgba(0,0,0,.08)}
.section-title{position:absolute;left:0;width:1200px;display:flex;justify-content:center;align-items:center;gap:22px;font-size:27px;color:var(--ink)}
.section-title::before,.section-title::after{content:"";width:44px;height:2px;background:var(--lime)}
.why-item{position:absolute;top:1617px;width:281px;height:317px;border-radius:18px;background:var(--white);box-shadow:0 2px 10px rgba(0,0,0,.07)}
.why-item .photo{left:12px;top:12px;width:257px;height:248px;border-radius:16px}
.why-item .label{position:absolute;left:0;right:0;top:278px;display:flex;justify-content:center;align-items:center;gap:14px;font-size:15.5px;font-weight:400;color:var(--ink);text-transform:uppercase}

/* steps */
.step-ring{position:absolute;width:160px;height:160px;border-radius:50%;background:var(--lime-pale);box-shadow:0 0 0 4px #fafbee}
.step-ring.active{background:var(--lime);box-shadow:0 0 0 8px var(--white),0 0 0 9px #555}
.step-ring svg{position:absolute;left:52px;top:52px;width:56px;height:56px}
.badge{position:absolute;width:38px;height:38px;border-radius:50%;background:var(--lime);color:var(--ink);font-size:14px;display:flex;align-items:center;justify-content:center;font-weight:400}
.badge.dark{background:var(--ink);color:var(--white)}
.step-text{position:absolute;top:2418px;width:360px;text-align:center}
.step-text h4{color:var(--lime);font-weight:400;font-size:17px;text-transform:uppercase;margin-bottom:18px}
.step-text p{font-size:15.5px;line-height:34px;color:var(--ink)}

/* projects */
.projects-bg{left:0;top:2597px;width:1200px;height:800px;background:var(--cream)}
.projects-intro{left:120px;top:2710px;width:960px;text-align:center;font-size:15.5px;line-height:33px;color:#333}
.project{position:absolute;top:2815px;height:343px;background:var(--white);border-radius:16px;box-shadow:0 2px 10px rgba(0,0,0,.06);overflow:hidden}
.project .photo{top:12px;height:275px;border-radius:14px}
.project .label{position:absolute;top:302px;left:0;right:0;text-align:center;font-size:15.5px;color:var(--ink);text-transform:uppercase;white-space:nowrap;font-weight:400}
.pager{position:absolute;top:3204px;width:32px;height:32px;border:1.5px solid var(--ink);border-radius:50%;display:flex;align-items:center;justify-content:center}

/* cta + footer */
.footer{left:0;top:3396px;width:1200px;height:341px;background:var(--ink)}
.cta{left:132px;top:3305px;width:934px;height:135px;background:var(--lime);border-radius:20px}
.cta-mark{left:172px;top:3348px;width:44px;height:44px;background:var(--ink)}
.cta-text{left:286px;top:3338px;font-size:19px;line-height:35px;color:var(--ink)}
.cta-btn{left:801px;top:3353px;width:229px;height:41px;background:var(--white)}
.footer-brand{left:0;width:1200px;top:3534px;text-align:center;font-family:"Orbitron",sans-serif;font-weight:600;font-size:20px;color:var(--white);text-transform:uppercase}
.footer-nav{left:0;width:1200px;top:3618px;display:flex;justify-content:center;gap:18px;color:var(--white);font-size:14.5px;text-transform:uppercase;font-weight:400}
.copyright{left:0;width:1200px;top:3672px;text-align:center;color:var(--white);font-size:13.5px;text-transform:uppercase;font-weight:400}
</style>
</head>
<body>

<!-- Header -->
<div class="abs brand-box">Bluegum Ridge<br>Earthworks</div>
<nav class="abs nav">
  <span class="active">Home</span><span>About Us</span><span>Projects</span><span>Contact Us</span>
</nav>
<a class="btn" style="left:918px;top:23px;width:170px;height:33px;font-size:12.5px">Request a quote
  <svg viewBox="0 0 12 12" fill="none" stroke="currentColor" stroke-width="1.4"><path d="M3 9 9 3M4 3h5v5"/></svg></a>

<!-- Hero -->
<div class="photo hero-photo" role="img" aria-label="Excavator digging soil at sunset on a construction site"></div>
<h1 class="abs display hero-title">Bluegum Ridge<br><span class="lime">Earthworks</span></h1>
<p class="abs hero-sub">Modern excavation for Perth’s next generation of builds</p>
<a class="btn" style="left:888px;top:312px;width:170px;height:39px">View projects
  <svg viewBox="0 0 12 12" fill="none" stroke="currentColor" stroke-width="1.4"><path d="M3 9 9 3M4 3h5v5"/></svg></a>

<!-- About -->
<div class="abs about-mark"></div>
<h2 class="abs display about-title">About <span class="lime">Bluegum Ridge<br>Earthworks</span></h2>
<p class="abs about-text" style="top:732px">Bluegum Ridge Earthworks is a Perth-based excavation and earthmoving company delivering precise, modern ground solutions for residential, commercial and development projects across Western Australia.</p>
<p class="abs about-text" style="top:876px">We exist to raise the standard of what earthworks should be — not just in how sites are moved, but in how projects are handled. The construction industry has evolved — and so should the companies that support it.</p>
<a class="btn" style="left:113px;top:1037px;width:161px;height:43px">Learn more
  <svg viewBox="0 0 12 12" fill="none" stroke="currentColor" stroke-width="1.4"><path d="M3 9 9 3M4 3h5v5"/></svg></a>
<div class="dots" style="left:426px;top:1054px;width:72px;height:50px"></div>
<div class="photo img-big" role="img" aria-label="Operator in hard hat and hi-vis vest seated in an excavator cab"></div>
<div class="photo img-small" role="img" aria-label="Site worker reviewing plans on a tablet overlooking a build site"></div>

<!-- Services -->
<div class="abs services"></div>
<div class="service" style="left:120px;width:250px">
  <svg viewBox="0 0 50 48" fill="none" stroke="#fff" stroke-width="1.6"><rect x="4" y="30" width="26" height="8" rx="4"/><path d="M8 30v-8h12v8M20 22l12-14 10 6-4 12"/><path d="M38 26l4 6-6 2"/><circle cx="9" cy="34" r="1.5"/><circle cx="17" cy="34" r="1.5"/><circle cx="25" cy="34" r="1.5"/></svg>
  <h3>Earthworks</h3>
  <p>We provide large-scale and detailed earthmoving services to shape and prepare land.</p>
</div>
<div class="service" style="left:405px;width:240px">
  <svg viewBox="0 0 50 48" fill="none" stroke="#fff" stroke-width="1.6"><path d="M4 44h40M6 44V12M6 20l16 12M22 32l8-4 4 8-10 2z"/><path d="M28 10l8-6 10 8-6 6"/><circle cx="36" cy="16" r="4" stroke="var(--lime)"/></svg>
  <h3>Excavation</h3>
  <p>Our excavation services cover everything from small residential footings.</p>
</div>
<div class="service" style="left:669px;width:200px">
  <svg viewBox="0 0 50 48" fill="none" stroke="#fff" stroke-width="1.6"><path d="M4 4v34M4 10h10v24M14 14h8"/><rect x="20" y="26" width="22" height="10" rx="3"/><path d="M24 26v-6h10l4 6"/><rect x="18" y="38" width="28" height="6" rx="3" stroke="var(--lime)"/></svg>
  <h3>Site Preparation</h3>
  <p>A strong project starts with a properly prepared site.</p>
</div>
<div class="service" style="left:917px;width:180px">
  <svg viewBox="0 0 50 48" fill="none" stroke="#fff" stroke-width="1.6"><path d="M4 28h42M4 34h42M4 40h42M12 28V18l12-6 8 4"/><path d="M32 16l6-10 6 6-6 4z"/><circle cx="36" cy="6" r="3" stroke="var(--lime)"/><path d="M10 22h8" stroke="var(--lime)"/></svg>
  <h3>Trenching &amp;<br>Drainage</h3>
  <p>We create clean, accurate trenches for plumbing.</p>
</div>

<!-- Why -->
<div class="abs why-card"></div>
<h2 class="section-title display" style="top:1545px">Why&nbsp;<span class="lime">Bluegum Ridge</span></h2>
<div class="why-item" style="left:160px">
  <div class="photo" role="img" aria-label="Yellow excavator parked beside a stockpile with pine trees behind" style="background:linear-gradient(170deg,#cfe0ee 0%,#5e7a4a 40%,#e0a21a 62%,#7a5a3a 100%)"></div>
  <div class="label">Modern equipment <svg width="20" height="10" viewBox="0 0 20 10" fill="none" stroke="#111" stroke-width="1.4"><path d="M0 5h18M14 1l4 4-4 4"/></svg></div>
</div>
<div class="why-item" style="left:460px">
  <div class="photo" role="img" aria-label="Excavator working on a city construction site under blue sky" style="background:linear-gradient(175deg,#9cc6e6 0%,#d9e6ef 45%,#e3b020 65%,#8a6a4a 100%)"></div>
  <div class="label">Reliable scheduling <svg width="20" height="10" viewBox="0 0 20 10" fill="none" stroke="#111" stroke-width="1.4"><path d="M0 5h18M14 1l4 4-4 4"/></svg></div>
</div>
<div class="why-item" style="left:759px">
  <div class="photo" role="img" aria-label="Aerial view of a loader filling a truck on grey gravel" style="background:linear-gradient(140deg,#6c6c6a 0%,#9a9894 50%,#5e5d5a 100%)"></div>
  <div class="label">Precision &amp; care <svg width="20" height="10" viewBox="0 0 20 10" fill="none" stroke="#111" stroke-width="1.4"><path d="M0 5h18M14 1l4 4-4 4"/></svg></div>
</div>
<a class="btn" style="left:490px;top:1984px;width:220px;height:42px">View more benefits
  <svg viewBox="0 0 12 12" fill="none" stroke="currentColor" stroke-width="1.4"><path d="M3 9 9 3M4 3h5v5"/></svg></a>

<!-- How it works -->
<div class="dots" style="left:46px;top:2134px;width:72px;height:50px"></div>
<h2 class="section-title display" style="top:2152px">How it&nbsp;<span class="lime">works</span></h2>

<div class="step-ring" style="left:174px;top:2231px">
  <svg viewBox="0 0 56 56" fill="none" stroke="#222" stroke-width="1.6"><rect x="16" y="6" width="32" height="40" rx="2"/><path d="M22 14h14M22 20h10M36 38v-8M41 38v-12M31 38v-4"/><circle cx="14" cy="40" r="7" stroke="var(--lime)"/><circle cx="14" cy="40" r="3" stroke="var(--lime)"/></svg>
</div>
<div class="badge" style="left:310px;top:2292px">01</div>
<svg class="abs" style="left:392px;top:2295px" width="84" height="22" viewBox="0 0 84 22" fill="none" stroke="var(--lime)" stroke-width="1.4"><path d="M2 16Q40 2 80 12M74 6l6 6-8 3"/></svg>

<div class="step-ring active" style="left:516px;top:2231px">
  <svg viewBox="0 0 56 56" fill="none" stroke="#fff" stroke-width="1.8"><rect x="10" y="8" width="32" height="42" rx="3"/><path d="M20 4h12v8H20zM16 22l3 3 5-6M16 34l3 3 5-6M28 22h8M28 34h4M36 44l14-16 4 4-14 16-6 2z"/></svg>
</div>
<div class="badge dark" style="left:652px;top:2292px">02</div>
<svg class="abs" style="left:734px;top:2295px" width="84" height="22" viewBox="0 0 84 22" fill="none" stroke="var(--lime)" stroke-width="1.4"><path d="M2 16Q40 2 80 12M74 6l6 6-8 3"/></svg>

<div class="step-ring" style="left:860px;top:2231px">
  <svg viewBox="0 0 56 56" fill="none" stroke="#222" stroke-width="1.6"><circle cx="26" cy="26" r="9"/><path d="M26 8v6M26 38v6M8 26h6M38 26h6M13 13l4 4M35 35l4 4M39 13l-4 4M13 39l4-4"/><path d="M6 20A22 22 0 0 1 44 12M46 32A22 22 0 0 1 8 40"/><circle cx="42" cy="42" r="8" stroke="var(--lime)"/><path d="M38 42l3 3 5-6" stroke="var(--lime)"/></svg>
</div>
<div class="badge" style="left:996px;top:2292px">03</div>

<div class="step-text" style="left:74px"><h4>Tell us about your project</h4><p>Share your site details, plans,<br>or scope of work.</p></div>
<div class="step-text" style="left:416px"><h4>We plan &amp; prepare</h4><p>Our team assesses the site,<br>equipment and timeline required.</p></div>
<div class="step-text" style="left:760px"><h4>We execute</h4><p>We arrive on site with the right<br>machinery and experienced operators.</p></div>
<div class="dots" style="left:1064px;top:2559px;width:72px;height:50px"></div>

<!-- Projects -->
<div class="abs projects-bg"></div>
<h2 class="section-title display" style="top:2652px">Our&nbsp;<span class="lime">projects</span></h2>
<p class="abs projects-intro">At <span class="lime">Bluegum Ridge Earthworks,</span> we take pride in delivering precise, high-quality earthmoving and excavation work across Perth. From residential developments to commercial sites, our projects showcase our expertise, reliability, and modern approach.</p>

<div class="project" style="left:-40px;width:343px">
  <div class="photo" role="img" aria-label="Workers laying blue pipes in a trench beside city towers" style="left:12px;width:319px;background:linear-gradient(160deg,#8db6d8 0%,#c98a4a 50%,#3b6fa8 75%,#7a5232 100%)"></div>
  <div class="label" style="left:-10px">Trenching – Joondalup</div>
</div>
<div class="project" style="left:334px;width:537px">
  <div class="photo" role="img" aria-label="Excavator clearing ground beside a brick house" style="left:12px;width:513px;background:linear-gradient(165deg,#dfe8ee 0%,#8a7a66 40%,#a0523a 60%,#6e5a3a 100%)"></div>
  <div class="label">Residential site prep – Subiaco</div>
</div>
<div class="project" style="left:903px;width:340px">
  <div class="photo" role="img" aria-label="Dump trucks moving earth on a dusty industrial site" style="left:9px;width:320px;background:linear-gradient(150deg,#8a8a86 0%,#bfae8a 45%,#d3a228 65%,#4a3e30 100%)"></div>
  <div class="label" style="text-align:left;left:95px">Industrial bulk excavation</div>
</div>
<div class="pager" style="left:548px"><svg width="10" height="12" viewBox="0 0 10 12" fill="none" stroke="#111" stroke-width="1.4"><path d="M7 1 2 6l5 5"/></svg></div>
<div class="pager" style="left:618px"><svg width="10" height="12" viewBox="0 0 10 12" fill="none" stroke="#111" stroke-width="1.4"><path d="M3 1l5 5-5 5"/></svg></div>

<!-- CTA & footer -->
<div class="abs footer"></div>
<div class="abs cta"></div>
<div class="abs cta-mark"></div>
<p class="abs display cta-text">Engineered ground solutions,<br>delivered on time</p>
<a class="btn cta-btn">Start your project
  <svg viewBox="0 0 12 12" fill="none" stroke="currentColor" stroke-width="1.4"><path d="M3 9 9 3M4 3h5v5"/></svg></a>

<div class="abs footer-brand">Bluegum Ridge Earthworks</div>
<nav class="abs footer-nav"><span>Home</span><span>|</span><span>About</span><span>|</span><span>Projects</span><span>|</span><span>Contact Us</span></nav>
<p class="abs copyright">© Bluegum Ridge Earthworks 2026 All rights reserved.</p>

</body>
</html>
```